Home Remodeling company needs a business card design

we need a business card design for home remodeling company in hamilton county, indiana USA. we offers a wide range of construction services including whole house renovations, Design and Build Basements and Kitchen and Bathroom Remodeling . we would like to see designs for both site of business card that use the same color of the company logo and also including all information below :
1- Karim Feltous CEO / General Contractor
2- all company contacts Telephone numbers ( 1-888-DULOM-47 ) ( 317-555-0193) email address ( info@dulomhome.com) website ( www.dulomhome.com ) and social media logos (Facebook- twitter- google plus )
3- company logo
4- licensed . insured . bonded

```html
<!DOCTYPE html>
<html lang="en">
<head>
<meta charset="utf-8">
<title>Dulom Home Remodeling – Business Card</title>
<link rel="stylesheet" href="https://fonts.googleapis.com/css2?family=Arimo:wght@400;700&display=swap">
<style>
  :root {
    --brand-red: #b72a36;
    --charcoal: #3b3b3d;
    --slate-grey: #8a8a8c;
    --paper: #f6f6f6;
    --backdrop: #e4e1dc;
    --icon-glyph: #ffffff;
  }
  * { margin: 0; padding: 0; box-sizing: border-box; }
  html, body {
    width: 1200px; height: 902px; overflow: hidden;
    background: var(--backdrop);
    font-family: "Arimo", Arial, sans-serif;
  }
  .canvas {
    position: relative; width: 1200px; height: 902px;
  }
  .card {
    position: absolute; left: 260px; width: 680px; height: 389px;
    box-shadow: 0 6px 18px rgba(0,0,0,0.18);
    overflow: hidden;
  }
  /* Back side */
  .card-back { top: 44px; background: var(--brand-red); }
  .back-lockup {
    position: absolute; left: 0; right: 0; top: 118px; text-align: center;
    color: #ffffff;
  }
  .back-lockup .brand-name {
    font-weight: 700; font-size: 104px; letter-spacing: 6px; line-height: 1;
  }
  .back-lockup .brand-line {
    margin-top: 10px; font-size: 22px; letter-spacing: 17px; padding-left: 17px;
  }
  /* Front side */
  .card-front { top: 470px; background: var(--paper); }
  .side-band {
    position: absolute; left: 0; top: 0; bottom: 0; width: 120px;
    background: var(--charcoal);
  }
  .side-rule {
    position: absolute; left: 128px; top: 0; bottom: 0; width: 3px;
    background: var(--brand-red);
  }
  .logo-frame {
    position: absolute; left: 128px; top: 40px; width: 26px; height: 96px;
    border-top: 3px solid var(--brand-red);
    border-bottom: 3px solid var(--brand-red);
    border-right: 3px solid var(--brand-red);
    border-radius: 0 4px 4px 0;
  }
  .front-lockup { position: absolute; left: 170px; top: 34px; }
  .front-lockup .brand-name {
    font-weight: 700; font-size: 68px; letter-spacing: 3px; line-height: 1;
    color: var(--charcoal);
  }
  .front-lockup .brand-line {
    margin-top: 6px; font-size: 17px; letter-spacing: 11px; color: var(--slate-grey);
  }
  .front-lockup .credentials {
    margin-top: 4px; font-size: 19px; letter-spacing: 1px; color: var(--slate-grey);
  }
  .person { position: absolute; left: 170px; top: 172px; }
  .person-name { color: var(--brand-red); font-size: 30px; line-height: 1.1; }
  .person-title { color: var(--charcoal); font-size: 20px; margin-top: 2px; }
  .contact-list {
    position: absolute; left: 170px; top: 250px; list-style: none;
  }
  .contact-item {
    display: flex; align-items: center; height: 29px;
    color: var(--brand-red); font-size: 19px;
  }
  .contact-icon {
    width: 20px; height: 20px; margin-right: 22px; flex: none;
  }
</style>
</head>
<body>
<main class="canvas">

  <section class="card card-back" aria-label="Card back">
    <div class="back-lockup">
      <div class="brand-name">DULOM</div>
      <div class="brand-line">HOME REMODELING</div>
    </div>
  </section>

  <section class="card card-front" aria-label="Card front">
    <div class="side-band"></div>
    <div class="side-rule"></div>
    <div class="logo-frame"></div>

    <div class="front-lockup">
      <div class="brand-name">DULOM</div>
      <div class="brand-line">HOME REMODELING</div>
      <div class="credentials">LICENSED . INSURED . BONDED</div>
    </div>

    <div class="person">
      <div class="person-name">Karim Feltous</div>
      <div class="person-title">CEO / General Contractor</div>
    </div>

    <ul class="contact-list">
      <li class="contact-item">
        <svg class="contact-icon" viewBox="0 0 20 20" aria-hidden="true">
          <rect width="20" height="20" fill="var(--brand-red)"/>
          <path d="M4 8c0-2 2-3 6-3s6 1 6 3l-2 1-1-2H7L6 9z M6 10h8l1 5H5z" fill="var(--icon-glyph)"/>
        </svg>
        1-888-DULOM-47
      </li>
      <li class="contact-item">
        <svg class="contact-icon" viewBox="0 0 20 20" aria-hidden="true">
          <rect width="20" height="20" fill="var(--brand-red)"/>
          <rect x="6" y="3" width="8" height="14" rx="1.5" fill="var(--icon-glyph)"/>
          <rect x="7.5" y="5" width="5" height="6" fill="var(--brand-red)"/>
        </svg>
        317-555-0193
      </li>
      <li class="contact-item">
        <svg class="contact-icon" viewBox="0 0 20 20" aria-hidden="true">
          <rect width="20" height="20" fill="var(--brand-red)"/>
          <rect x="3" y="5.5" width="14" height="9" fill="var(--icon-glyph)"/>
          <path d="M3 5.5l7 5 7-5" fill="none" stroke="var(--brand-red)" stroke-width="1.2"/>
        </svg>
        info@dulomhome.com
      </li>
      <li class="contact-item">
        <svg class="contact-icon" viewBox="0 0 20 20" aria-hidden="true">
          <rect width="20" height="20" fill="var(--brand-red)"/>
          <circle cx="10" cy="10" r="6" fill="none" stroke="var(--icon-glyph)" stroke-width="1.5"/>
          <path d="M4 10h12 M10 4c-3 3-3 9 0 12 M10 4c3 3 3 9 0 12" fill="none" stroke="var(--icon-glyph)" stroke-width="1.1"/>
        </svg>
        www.dulomhome.com
      </li>
    </ul>
  </section>

</main>
</body>
</html>
```